Brightmill Data Works

Our company is about IT hardwares and IT solutions. IT hardware such as PC, RAMS, storage and servers. IT solutions such as project management, BA. We are also selling new technology too.

Target Market(s)

Consumer, Small to Medium Business, Corporate

Requirements
Must have
• The business card must have the following:
• Name:
• Title:
• Contact Number:
• Email address:
• Website:
• Color: Must match the logo color upgrade

```html
<!DOCTYPE html>
<html lang="en">
<head>
<meta charset="utf-8">
<title>Brightmill Data Works — Business Card</title>
<link rel="stylesheet" href="https://fonts.googleapis.com/css2?family=Exo+2:wght@600;700&family=Arimo:wght@400&display=swap">
<style>
  :root {
    --canvas: #d6d6d6;
    --slate: #5a5a5b;
    --slate-dark: #4a4a4b;
    --paper: #f4f4f3;
    --amber: #e3a245;
    --amber-deep: #c8702a;
    --ink-light: #f2f2f2;
    --ink-dark: #505051;
  }
  * { margin: 0; padding: 0; box-sizing: border-box; }
  html, body { width: 1200px; height: 864px; overflow: hidden; }
  body {
    background: var(--canvas);
    position: relative;
    font-family: "Arimo", Arial, sans-serif;
  }
  .card {
    position: absolute;
    width: 600px;
    height: 343px;
    overflow: hidden;
    box-shadow: 0 6px 18px rgba(0,0,0,0.18);
  }

  /* Back side */
  .card-back { left: 520px; top: 70px; background: var(--paper); }
  .card-back .top-field {
    position: absolute; left: 0; top: 0; width: 100%; height: 150px;
    background: linear-gradient(135deg, var(--slate-dark), var(--slate));
    border-bottom: 4px solid var(--amber);
  }
  .card-back .top-field .mark {
    position: absolute; left: 50%; top: 50%;
    width: 44px; height: 44px; margin: -22px 0 0 -22px;
    background: var(--amber);
  }
  .card-back .wordmark {
    position: absolute; left: 0; right: 0; top: 215px;
    text-align: center;
    font-family: "Exo 2", sans-serif; font-weight: 700;
    font-size: 38px; letter-spacing: 1px; text-transform: uppercase;
    color: var(--ink-dark);
  }

  /* Front side */
  .card-front {
    left: 80px; top: 450px;
    background: linear-gradient(135deg, var(--slate-dark), #626263 45%, var(--slate-dark));
  }
  .card-front .wordmark {
    position: absolute; left: 30px; top: 95px; width: 300px;
    font-family: "Exo 2", sans-serif; font-weight: 700;
    font-size: 32px; line-height: 1.05; text-transform: uppercase;
    color: var(--ink-light); text-align: center;
  }
  .card-front .divider {
    position: absolute; left: 350px; top: 28px; width: 1px; height: 200px;
    background: linear-gradient(to bottom, transparent, rgba(255,255,255,0.6), transparent);
  }
  .card-front .person { position: absolute; left: 380px; top: 62px; }
  .person-name {
    font-family: "Exo 2", sans-serif; font-weight: 600;
    font-size: 20px; color: var(--ink-light); text-transform: uppercase;
    letter-spacing: 0.5px;
  }
  .person-title {
    font-family: "Exo 2", sans-serif; font-weight: 600;
    font-size: 15px; color: var(--amber); text-transform: uppercase;
    margin-top: -2px;
  }
  .contact-list {
    position: absolute; left: 380px; top: 142px; list-style: none;
  }
  .contact-list li {
    display: flex; align-items: center; gap: 10px;
    font-size: 14px; color: var(--ink-light); height: 22px;
  }
  .contact-list .icon {
    width: 15px; height: 15px; background: var(--amber);
    display: flex; align-items: center; justify-content: center; flex: none;
  }
  .card-front .band {
    position: absolute; left: 0; bottom: 32px; width: 100%; height: 72px;
    background: linear-gradient(90deg, var(--amber), #dd9a42 50%, var(--amber-deep));
  }
</style>
</head>
<body>

<section class="card card-back" aria-label="Card back">
  <div class="top-field"><span class="mark"></span></div>
  <p class="wordmark">Brightmill Data Works</p>
</section>

<section class="card card-front" aria-label="Card front">
  <p class="wordmark">Brightmill Data Works</p>
  <span class="divider"></span>
  <div class="person">
    <p class="person-name">Owen Halvard</p>
    <p class="person-title">Manager</p>
  </div>
  <ul class="contact-list">
    <li>
      <span class="icon"><svg width="9" height="9" viewBox="0 0 10 10"><path d="M2 1 L4 1 L4.6 3 L3.4 4 Q4.5 6 6 6.6 L7 5.4 L9 6 L9 8 Q8.5 9 7 9 Q1 8 1 3 Q1 1.5 2 1Z" fill="#fff"/></svg></span>
      +1-555-204-7718
    </li>
    <li>
      <span class="icon"><svg width="10" height="8" viewBox="0 0 10 8"><rect x="0.5" y="0.5" width="9" height="7" fill="none" stroke="#fff"/><path d="M0.5 0.5 L5 4.5 L9.5 0.5" fill="none" stroke="#fff"/></svg></span>
      owen@brightmilldata.com
    </li>
    <li>
      <span class="icon"><svg width="10" height="10" viewBox="0 0 10 10"><circle cx="5" cy="5" r="4.2" fill="none" stroke="#fff"/><ellipse cx="5" cy="5" rx="1.8" ry="4.2" fill="none" stroke="#fff"/><path d="M0.8 5 H9.2" stroke="#fff"/></svg></span>
      www.brightmilldata.com
    </li>
  </ul>
  <div class="band"></div>
</section>

</body>
</html>
```